Borvik Media - Amazing Homepage

We would like to build an amazing homepage for our site. We will need it built in HTM5, so it works across devices and would like it to parallax scroll , so it looks amazing.
We are a digital media agency, that has recently launched. Our old site is self build through one of the standard web build sites. We will be hosting our new site independently.
This is our old site - www.borvik-media.example
The new site only really needs one scrolling page to explain what we do and have our contact details at the bottom.
We have a place to host it, once designed. So we can share with the final design for you to upload.
Attached are:
Brief
Logos and artwork
Our PowerPoint template to give you an idea of colours

```html
<!DOCTYPE html>
<html lang="en">
<head>
<meta charset="utf-8">
<title>Borvik Media – We Make Amazing</title>
<link rel="stylesheet" href="https://fonts.googleapis.com/css2?family=PT+Sans:wght@400;700&family=Roboto:wght@400;500&display=swap">
<style>
:root{
  --gold:#bf9a35;
  --gold-dark:#a98628;
  --ink:#2b2b2b;
  --grey:#6e6e6e;
  --charcoal:#242222;
  --white:#ffffff;
  --rule:#e3e3e3;
}
*{box-sizing:border-box;margin:0;padding:0}
html,body{width:1200px;height:4186px;overflow:hidden;background:var(--white)}
body{font-family:"PT Sans",sans-serif;color:var(--ink)}
.section{position:absolute;left:0;width:1200px;text-align:center}
.abs{position:absolute}
.chevron{position:absolute;left:582px;width:36px;height:20px}

/* header */
.site-header{top:0;height:117px;border-top:3px solid var(--gold);background:var(--white)}
.brand{position:absolute;left:128px;top:24px;display:flex;align-items:center;gap:12px}
.brand-dot{width:60px;height:60px;border-radius:50%;border:3px solid var(--gold)}
.brand-name{font-size:22px;letter-spacing:3px;color:#555;font-weight:400}
.nav{position:absolute;left:508px;top:33px;display:flex;align-items:center;font-family:"Roboto",sans-serif;font-size:16px;color:#444}
.nav a{color:inherit;text-decoration:none}
.nav .active{background:var(--gold);color:var(--white);width:96px;height:52px;line-height:52px;text-align:center}
.nav .item{margin-left:58px}

/* hero */
.hero{top:117px;height:419px;background:linear-gradient(180deg,#2e3e48 0%,#1c272e 55%,#0f1418 100%);color:var(--white)}
.hero h1{position:absolute;top:98px;width:100%;font-size:56px;font-weight:400;letter-spacing:1px}
.hero p{position:absolute;top:184px;width:100%;font-size:40px}
.dots{position:absolute;top:366px;left:562px;display:flex;gap:8px}
.dots span{width:14px;height:14px;border-radius:50%;background:#ddd;border:2px solid #999}
.dots span.on{background:var(--gold)}

/* clarity */
.clarity{top:536px;height:575px}
.gold-heading{color:var(--gold);font-size:32px;line-height:1.4}
.clarity .gold-heading{position:absolute;top:30px;width:100%}
.offer{position:absolute;top:128px;width:230px;text-align:center}
.offer-icon{width:112px;height:112px;border-radius:50%;border:3px solid var(--gold);margin:0 auto;display:flex;align-items:center;justify-content:center}
.offer p{margin-top:26px;font-family:"Roboto",sans-serif;font-size:14px;line-height:22px;color:var(--grey)}
.motto{position:absolute;top:436px;width:100%;font-size:25px;color:var(--ink)}

/* gold bands */
.band-gold{background:var(--gold);color:var(--white)}
.band-heading{font-size:32px;line-height:46px}
.fairness{top:1111px;height:530px}
.fairness .band-heading{position:absolute;top:34px;width:100%}
.photo{position:absolute;top:159px;width:332px;height:217px}
.caption{position:absolute;top:400px;width:332px;font-size:24px}

/* coup */
.coup{top:1641px;height:614px}
.coup .gold-heading{position:absolute;top:40px;left:150px;width:900px;font-size:31px;line-height:46px}
.crate{position:absolute;top:214px;left:380px;width:440px;height:280px}

.quiet{top:2255px;height:220px;background:var(--charcoal);color:var(--white)}
.quiet h2{position:absolute;top:40px;width:100%;font-size:62px;font-weight:400}
.quiet em{font-style:normal;color:var(--gold)}

/* specialists */
.specialists{top:2475px;height:595px}
.specialists .gold-heading{position:absolute;top:44px;left:150px;width:900px;font-size:31px;line-height:44px}
.specialists .lead{position:absolute;top:152px;left:130px;width:940px;font-family:"Roboto",sans-serif;font-size:18px;line-height:50px;color:#444}
.services{position:absolute;top:275px;left:110px;width:980px;display:flex;justify-content:space-between}
.service{width:140px;text-align:center}
.service svg{width:84px;height:84px}
.service span{display:block;margin-top:14px;font-family:"Roboto",sans-serif;font-size:19px;color:var(--gold)}
.board{position:absolute;top:462px;width:100%;font-family:"Roboto",sans-serif;font-size:18px;color:#444}

/* results */
.results{top:3070px;height:474px}
.results .band-heading{position:absolute;top:44px;left:150px;width:900px;font-size:31px;line-height:46px}
.results .brand-big{position:absolute;top:240px;left:394px;display:flex;align-items:center;gap:22px}
.brand-big .brand-dot{width:140px;height:140px;border-color:#4a4a4a;border-width:4px}
.brand-big .brand-name{font-size:40px;letter-spacing:6px;color:#4a4a4a}

/* clients */
.clients{top:3544px;height:307px}
.clients .gold-heading{position:absolute;top:40px;width:100%;font-size:31px}
.client-row{position:absolute;top:130px;left:128px;width:944px;display:flex;justify-content:space-between;align-items:center}
.client{font-size:30px;font-weight:700;color:#555}

/* contact */
.contact{top:3851px;height:257px}
.contact .band-heading{position:absolute;top:36px;left:150px;width:900px;font-size:31px;line-height:46px}
.contact address{position:absolute;top:146px;width:100%;font-style:normal;font-family:"Roboto",sans-serif;font-size:20px;line-height:28px}

.site-footer{top:4108px;height:78px;background:var(--charcoal);color:#ccc;text-align:left}
.site-footer small{position:absolute;left:130px;top:30px;font-family:"Roboto",sans-serif;font-size:14px}
.social{position:absolute;left:948px;top:26px;display:flex;gap:14px}
.social span{width:26px;height:26px;border-radius:50%;background:#eee}
</style>
</head>
<body>

<header class="section site-header">
  <div class="brand"><span class="brand-dot"></span><span class="brand-name">BORVIK MEDIA</span></div>
  <nav class="nav">
    <a class="active" href="#">Home</a>
    <a class="item" href="#">What we can offer</a>
    <a class="item" href="#">Contact Us</a>
    <svg class="item" width="18" height="18" viewBox="0 0 18 18"><circle cx="7" cy="7" r="5.5" fill="none" stroke="#bf9a35" stroke-width="2"/><line x1="11" y1="11" x2="16" y2="16" stroke="#bf9a35" stroke-width="2.4"/></svg>
  </nav>
</header>

<section class="section hero" role="img" aria-label="Photo of a business team standing together in a dark office">
  <h1>GOT THE FEELING YOUR</h1>
  <p>Your Digital Marketing Just Isn’t Quite ‘there’</p>
  <div class="dots"><span></span><span class="on"></span><span class="on"></span><span class="on"></span></div>
</section>

<section class="section clarity">
  <h2 class="gold-heading" style="font-weight:400">We keep fighting to give you clarity by</h2>
  <div class="offer" style="left:117px">
    <div class="offer-icon"><svg width="60" height="60" viewBox="0 0 60 60" fill="none" stroke="#2b2b2b" stroke-width="3"><circle cx="26" cy="26" r="18"/><path d="M8 26h36M26 8c-8 10-8 26 0 36M26 8c8 10 8 26 0 36"/><circle cx="42" cy="42" r="7" fill="#fff"/><line x1="47" y1="47" x2="54" y2="54"/></svg></div>
    <p>Creating a singular view of your digital eco system</p>
  </div>
  <div class="offer" style="left:345px">
    <div class="offer-icon"><svg width="62" height="56" viewBox="0 0 62 56"><ellipse cx="30" cy="32" rx="24" ry="18" fill="#2b2b2b"/><rect x="14" y="44" width="8" height="10" fill="#2b2b2b"/><rect x="38" y="44" width="8" height="10" fill="#2b2b2b"/><circle cx="30" cy="12" r="9" fill="#2b2b2b"/><text x="30" y="16" font-size="12" fill="#fff" text-anchor="middle" font-family="Roboto,sans-serif">$</text></svg></div>
    <p>Reviewing how and why your money is being spent when it is</p>
  </div>
  <div class="offer" style="left:591px">
    <div class="offer-icon"><svg width="62" height="56" viewBox="0 0 62 56" fill="#2b2b2b"><circle cx="31" cy="9" r="7"/><circle cx="11" cy="36" r="6"/><circle cx="31" cy="36" r="6"/><circle cx="51" cy="36" r="6"/><path d="M2 56c0-10 18-10 18 0zM22 56c0-10 18-10 18 0zM42 56c0-10 18-10 18 0z"/><path d="M31 18v10M11 30v-6h40v6" stroke="#2b2b2b" stroke-width="2.5" fill="none"/></svg></div>
    <p>Profiling your customers. Who doesn’t have 1000’s of different customers with different motivations, interests and value to the brand?</p>
  </div>
  <div class="offer" style="left:839px">
    <div class="offer-icon"><svg width="60" height="56" viewBox="0 0 60 56" fill="none" stroke="#2b2b2b" stroke-width="3"><rect x="4" y="6" width="52" height="36" rx="2"/><path d="M22 52h16M30 42v10"/><circle cx="30" cy="24" r="9"/><path d="M27 19l8 5-8 5z" fill="#2b2b2b"/></svg></div>
    <p>Finding the best digital channels to communicate with them because everything is changing every day...exciting isn’t it!</p>
  </div>
  <p class="motto">Never stop, never settle, always improve.&nbsp; Be amazing.</p>
  <svg class="chevron" style="top:504px" viewBox="0 0 36 20"><path d="M3 3l15 14L33 3" fill="none" stroke="#bf9a35" stroke-width="5"/></svg>
</section>

<section class="section band-gold fairness">
  <h2 class="band-heading" style="font-weight:400">Every client deserves amazing work, regardless of<br>the brand, it’s all real money</h2>
  <div class="photo" style="left:234px;background:radial-gradient(circle at 35% 45%,#3b7fc4,#1b3b6e 45%,#7a2a1e 80%)" role="img" aria-label="Close-up photo of colourful glass marbles"></div>
  <div class="photo" style="left:639px;background:linear-gradient(180deg,#1a1e14 0%,#2d4a1c 60%,#4f7a2a 100%)" role="img" aria-label="Photo of a football resting on grass"></div>
  <p class="caption" style="left:234px">Marbles</p>
  <p class="caption" style="left:639px">Football Stickers</p>
  <svg class="chevron" style="top:464px" viewBox="0 0 36 20"><path d="M3 3l15 14L33 3" fill="none" stroke="#fff" stroke-width="5"/></svg>
</section>

<section class="section coup">
  <h2 class="gold-heading" style="font-weight:400">It’s time to start a coup...there are too many large agency networks, too few agencies being transparent, too many putting quality of work second to income</h2>
  <div class="crate" style="background:linear-gradient(180deg,#b9b3aa 0%,#8a5a36 30%,#6b3f22 100%)" role="img" aria-label="Photo of a wooden soap crate"></div>
  <svg class="chevron" style="top:550px" viewBox="0 0 36 20"><path d="M3 3l15 14L33 3" fill="none" stroke="#bf9a35" stroke-width="5"/></svg>
</section>

<section class="section quiet">
  <h2>Well, a <em>very quiet</em> coup.</h2>
  <svg class="chevron" style="top:174px" viewBox="0 0 36 20"><path d="M3 3l15 14L33 3" fill="none" stroke="#fff" stroke-width="5"/></svg>
</section>

<section class="section specialists">
  <h2 class="gold-heading" style="font-weight:400">We’ve yet to come across a client that wants to shrink... making us specialists in delivering growth!</h2>
  <p class="lead">We’ve been optimising our digital knowledge for over 20 years and we genuinely know what we are talking about</p>
  <div class="services">
    <div class="service"><svg viewBox="0 0 84 84" fill="none" stroke="#2b2b2b" stroke-width="4"><circle cx="34" cy="30" r="24" stroke-width="3"/><circle cx="34" cy="30" r="14" stroke-width="3"/><path d="M30 30v34l10-6 8 20 8-4-8-18 12-2z" fill="#2b2b2b"/></svg><span>PPC</span></div>
    <div class="service"><svg viewBox="0 0 84 84" fill="none" stroke="#2b2b2b" stroke-width="4"><rect x="6" y="10" width="72" height="48"/><path d="M16 48l16-16 12 10 22-22"/><path d="M42 58v20M28 80l14-22 14 22"/></svg><span>SEO</span></div>
    <div class="service"><svg viewBox="0 0 84 84"><rect x="6" y="6" width="56" height="56" fill="#2b2b2b"/><path d="M70 22v56H22" fill="none" stroke="#2b2b2b" stroke-width="6"/></svg><span>DISPLAY</span></div>
    <div class="service"><svg viewBox="0 0 84 84" fill="none" stroke="#2b2b2b" stroke-width="4"><ellipse cx="42" cy="14" rx="30" ry="9"/><path d="M12 14v56c0 12 60 12 60 0V14M12 32c0 12 60 12 60 0M12 51c0 12 60 12 60 0"/></svg><span>MANAGEMENT</span></div>
    <div class="service"><svg viewBox="0 0 84 84" fill="#2b2b2b"><circle cx="18" cy="14" r="9"/><circle cx="42" cy="14" r="9"/><circle cx="66" cy="14" r="9"/><rect x="8" y="27" width="20" height="34" rx="5"/><rect x="32" y="27" width="20" height="34" rx="5"/><rect x="56" y="27" width="20" height="34" rx="5"/><rect x="11" y="58" width="6" height="22"/><rect x="19" y="58" width="6" height="22"/><rect x="35" y="58" width="6" height="22"/><rect x="43" y="58" width="6" height="22"/><rect x="59" y="58" width="6" height="22"/><rect x="67" y="58" width="6" height="22"/></svg><span>PAID SOCIAL</span></div>
    <div class="service"><svg viewBox="0 0 84 84" fill="none" stroke="#2b2b2b" stroke-width="4"><rect x="14" y="10" width="56" height="70" rx="3"/><rect x="30" y="4" width="24" height="12" fill="#2b2b2b"/><path d="M24 32h36M24 46h36M24 60h36"/></svg><span>ATTRIBUTION</span></div>
  </div>
  <p class="board">Operating at board level in top 10 digital agencies</p>
  <svg class="chevron" style="top:532px" viewBox="0 0 36 20"><path d="M3 3l15 14L33 3" fill="none" stroke="#bf9a35" stroke-width="5"/></svg>
</section>

<section class="section band-gold results">
  <h2 class="band-heading" style="font-weight:400">Happily, we smash it for all our clients, with an average of 35% improvement in performance within the first quarter of working with us</h2>
  <div class="brand-big"><span class="brand-dot"></span><span class="brand-name">BORVIK</span></div>
</section>

<section class="section clients">
  <h2 class="gold-heading" style="font-weight:400">Logos of Clients</h2>
  <div class="client-row">
    <span class="client">Hartley &amp; Co</span>
    <span class="client">Calmora</span>
    <span class="client">Veloura</span>
    <span class="client">Stagecroft</span>
    <span class="client">Nimbus</span>
  </div>
  <svg class="chevron" style="top:240px" viewBox="0 0 36 20"><path d="M3 3l15 14L33 3" fill="none" stroke="#bf9a35" stroke-width="5"/></svg>
</section>

<section class="section band-gold contact">
  <h2 class="band-heading" style="font-weight:400">If you are still reading our rant then get in touch / follow us / let’s go for a coffee</h2>
  <address>Our address is 14 Fenwick Row, London, E1 7QX<br>Contact@borvik-media.example</address>
</section>

<footer class="section site-footer">
  <small>Copyright @ 2014 Borvikmedia. All Rights Reserved.</small>
  <div class="social" aria-label="Social links"><span></span><span></span><span></span></div>
</footer>

</body>
</html>
```